Refresh of far from plain IT company website

Our web site is starting to show it's age. You can see the existing site here: www.plumbwick.net. As a growing company we want to come across as a dynamic collection of IT experts.

We want to update the design so are open to any colour palette and look, but want to retain our current table logo. We use the logo on our business cards but with a white background - see the attached file, so you don't need to keep the brown or the green.

The design should consider the range of browsers that will be looking at the site - so please show how it will look on a wide screen laptop and a 768x1024 tablet.

We want to add some pages about our team and their skills, probably with photos of each person on the team.

This is an uncoded project - the PSD files of the design is required, not coding.
Updates

Thanks everyone for the submissions so far.  It's a holiday day in the UK today but we will get some feedback on the designs so far out to you.

Target Market(s)

Architects and other creative types looking for IT support

Industry/Entity Type

Business

Font styles to use
Serif
Sans Serif

Requirements
Must have
• Must look good on a laptop and an iPad.

```html
<!DOCTYPE html>
<html lang="en">
<head>
<meta charset="utf-8">
<title>plumbwick – Serious IT support for business</title>
<link href="https://fonts.googleapis.com/css2?family=Ubuntu:wght@400;500;700&family=Open+Sans:wght@400;600&family=Roboto+Condensed:wght@700&family=Lobster&display=swap" rel="stylesheet">
<style>
:root{
  --plum:#93004c;
  --gold:#d8ae00;
  --gold-light:#f0c419;
  --ink:#333;
  --muted:#666;
  --nav:#3a3a3a;
  --nav-line:#555;
  --line:#ddd;
  --white:#fff;
}
*{box-sizing:border-box;margin:0;padding:0}
html,body{width:1043px;height:1200px;overflow:hidden;background:var(--white)}
body{font-family:"Open Sans",sans-serif;color:var(--ink)}
.page{width:1280px;height:1472px;transform:scale(.81484);transform-origin:0 0;position:relative;overflow:hidden}
.top-rule{position:absolute;left:0;top:0;width:1280px;height:5px;background:var(--gold)}
.live-chat{position:absolute;left:1000px;top:5px;width:140px;height:26px;background:var(--gold);color:var(--plum);font:500 15px "Ubuntu",sans-serif;display:flex;align-items:center;justify-content:center;gap:10px}
.brand{position:absolute;left:140px;top:28px;display:flex;align-items:center;gap:22px}
.brand-mark{width:98px;height:66px;background:var(--gold)}
.brand-name{font:500 62px "Ubuntu",sans-serif;color:var(--plum);letter-spacing:-1px}
.call{position:absolute;right:140px;top:58px;display:flex;align-items:center;gap:10px}
.call small{display:block;color:var(--gold);font:500 14px "Ubuntu",sans-serif}
.call strong{display:block;color:var(--plum);font:500 26px "Ubuntu",sans-serif}
.nav{position:absolute;left:140px;top:133px;width:1000px;height:33px;display:flex;background:linear-gradient(#4a4a4a,#2e2e2e);list-style:none}
.nav li{flex:auto;color:var(--white);font:500 14px "Ubuntu",sans-serif;display:flex;align-items:center;justify-content:center;border-left:1px solid var(--nav-line);letter-spacing:.5px}
.nav li.active{background:var(--gold);color:var(--plum);border:none;flex:0 0 103px}
.hero{position:absolute;left:0;top:166px;width:1280px;height:488px;background:linear-gradient(#a8a8a8,#5a5a5a 55%,#050505)}
.hero-photo{position:absolute;left:690px;top:40px;width:460px;height:340px;background:radial-gradient(ellipse at 50% 40%,#e8e8ea,#6d6f75 70%,transparent 72%)}
.hero-script{position:absolute;left:140px;top:52px;font:44px "Lobster",serif;color:var(--white)}
.hero h1{position:absolute;left:144px;top:114px;font:500 31px "Ubuntu",sans-serif;color:var(--white)}
.hero p{position:absolute;left:144px;top:162px;font:400 18px/27px "Open Sans",sans-serif;color:var(--white)}
.read-more{position:absolute;left:140px;top:267px;width:211px;height:54px;border-radius:4px;background:linear-gradient(var(--gold-light),var(--gold));color:var(--white);font:700 24px "Roboto Condensed",sans-serif;display:flex;align-items:center;justify-content:center}
.arrow-btn{position:absolute;top:194px;width:50px;height:50px;border-radius:50%;background:#111;border:2px solid #777;color:var(--white);font:700 30px sans-serif;display:flex;align-items:center;justify-content:center}
.services{position:absolute;left:140px;top:545px;width:1000px;height:160px;background:var(--white);border:1px solid var(--line)}
.services-tab{position:absolute;left:544px;top:524px;width:192px;height:42px;background:linear-gradient(#fff,#e6e6e6);border-radius:6px 6px 0 0;font:700 25px "Roboto Condensed",sans-serif;color:#444;display:flex;align-items:center;justify-content:center}
.service{position:absolute;top:30px;text-align:center;font:500 15px "Ubuntu",sans-serif;color:#333;width:240px}
.service i{display:block;width:62px;height:62px;border-radius:50%;background:var(--gold);margin:0 auto 24px;position:relative}
.service i::after{content:"";position:absolute;left:19px;top:19px;width:24px;height:24px;border-radius:4px;background:var(--plum)}
.svc-arrow{position:absolute;top:72px;color:#555;font:700 22px sans-serif}
.welcome-mark{position:absolute;left:143px;top:731px;width:72px;height:48px;background:var(--gold)}
.welcome h2{position:absolute;left:232px;top:744px;font:500 21px "Ubuntu",sans-serif;color:#333}
.welcome h2 span{color:var(--plum);font-size:27px}
.welcome hr{position:absolute;left:142px;top:794px;width:634px;border:none;border-top:1px dotted #999}
.welcome p{position:absolute;left:142px;width:634px;font:14px/20.5px "Open Sans",sans-serif;color:var(--muted);text-align:justify;letter-spacing:.3px}
.welcome a{position:absolute;left:682px;top:941px;font:700 14px "Ubuntu",sans-serif;color:var(--plum)}
.video{position:absolute;left:802px;top:748px;width:338px;height:180px;background:linear-gradient(#eef0f2,#8a8c92 60%,#2a2a2a)}
.video-bar{position:absolute;left:802px;top:928px;width:338px;height:18px;background:linear-gradient(#eee,#bbb);font:9px "Open Sans",sans-serif;color:#333;padding:3px 0 0 50px}
.news{position:absolute;left:140px;top:1024px;width:1000px;height:60px;border:1px solid #ccc;border-radius:4px;background:linear-gradient(#fff,#e9e9e9)}
.news-date{position:absolute;left:15px;top:9px;width:44px;height:44px;background:var(--plum);color:var(--white);text-align:center;font:700 18px "Ubuntu",sans-serif}
.news-date b{display:block;background:var(--gold);font-size:12px;line-height:15px}
.news p{position:absolute;left:114px;top:7px;width:875px;font:14px/21px "Open Sans",sans-serif;color:var(--muted)}
.news p strong{color:#444;font-weight:600}
.news a{position:absolute;right:18px;top:36px;font:700 14px "Ubuntu",sans-serif;color:var(--plum)}
.footer{position:absolute;left:0;top:1122px;width:1280px;height:300px;background:var(--plum);color:var(--white)}
.footer h3{position:absolute;font:400 20px "Ubuntu",sans-serif}
.quick-links{position:absolute;left:140px;top:58px;list-style:none;display:grid;grid-template-columns:132px 132px;row-gap:20px;font:500 13px "Ubuntu",sans-serif}
.quick-links li::before{content:"›";color:var(--gold);margin-right:10px}
.field{position:absolute;left:424px;width:255px;height:28px;background:var(--white);border:1px solid #ccc;border-radius:3px;font:12px "Open Sans",sans-serif;color:#999;padding:5px 14px}
.btn{position:absolute;background:var(--gold);color:var(--white);font:700 15px "Ubuntu",sans-serif;border-radius:3px;display:flex;align-items:center;justify-content:center}
.divider{position:absolute;top:30px;width:1px;height:160px;background:rgba(255,255,255,.25)}
.info{position:absolute;left:730px;font:14px/17px "Ubuntu",sans-serif;display:flex;gap:14px}
.info svg{flex:none}
.footer-mark{position:absolute;left:985px;top:66px;width:152px;height:105px;background:rgba(255,255,255,.25)}
.newsletter{position:absolute;left:279px;top:244px;width:259px;height:32px;background:var(--white);border-radius:3px;font:14px "Open Sans",sans-serif;color:#999;padding:7px 14px}
.social{position:absolute;top:244px;width:28px;height:28px;background:rgba(255,255,255,.85);border-radius:3px}
.copyright{position:absolute;left:0;top:1422px;width:1280px;height:50px;background:var(--gold);font:400 16px "Ubuntu",sans-serif;color:#333;display:flex;align-items:center;justify-content:center}
</style>
</head>
<body>
<div class="page">
  <div class="top-rule"></div>
  <div class="live-chat">
    <svg width="24" height="18" viewBox="0 0 24 18"><path d="M3 2h13a2 2 0 0 1 2 2v6a2 2 0 0 1-2 2H8l-4 4v-4H3a2 2 0 0 1-2-2V4a2 2 0 0 1 2-2z" fill="none" stroke="#93004c" stroke-width="2"/></svg>
    LIVE CHAT
  </div>

  <header class="brand">
    <div class="brand-mark" role="img" aria-label="Company table logo"></div>
    <div class="brand-name">plumbwick</div>
  </header>

  <div class="call">
    <svg width="22" height="42" viewBox="0 0 22 42"><path d="M14 2c-8 2-12 10-12 19s4 17 12 19l3-7c-5-2-7-7-7-12s2-10 7-12z" fill="#111"/></svg>
    <div><small>Call Us</small><strong>020 4410 2286</strong></div>
  </div>

  <ul class="nav">
    <li class="active">HOME</li><li>ABOUT US</li><li>WHAT WE DO</li><li>NEWS BLOG</li><li>ARTICLES</li><li>CLIENTS</li><li>PARTNERS</li><li>CONTACT US</li>
  </ul>

  <section class="hero">
    <div class="hero-photo" role="img" aria-label="Photo of a smiling business team with arms crossed"></div>
    <div class="hero-script">Serious IT support for business</div>
    <h1>Lorem ipsum dolor sit amet</h1>
    <p>Lorem ipsum dummy text for the for the lorem ips<br>Lorem ipsum dummy text for the for the<br>Lorem ipsum dummy text for the for the lorem</p>
    <div class="read-more">READ MORE</div>
    <div class="arrow-btn" style="left:62px">‹</div>
    <div class="arrow-btn" style="left:1180px">›</div>
  </section>

  <section class="services">
    <span class="svc-arrow" style="left:8px">‹</span>
    <div class="service" style="left:27px"><i></i>IT Support &amp; Management</div>
    <div class="service" style="left:299px"><i></i>Cloud Computing</div>
    <div class="service" style="left:541px"><i></i>Disaster Recovery</div>
    <div class="service" style="left:769px"><i></i>Virtualisation</div>
    <span class="svc-arrow" style="right:8px">›</span>
  </section>
  <div class="services-tab">Our Services</div>

  <section class="welcome">
    <div class="welcome-mark" role="img" aria-label="Company table logo"></div>
    <h2>Welcome to <span>plumbwick</span></h2>
    <hr>
    <p style="top:802px">Plumbwick was established with a specific aim: to consistently deliver an advanced and comprehensive IT service for ambitious growing companies across many industry sectors. We aim to provide the very best in service and support, and to aid business growth through the effective and skilled use of modern IT solutions</p>
    <p style="top:892px">Founded in 2003, we have grown rapidly and have delivered successful business solutions to small and medium sized businesses, working with customers across a wide IT spectrum. The knowledge, experience and expertise.</p>
    <a>Read more »</a>
  </section>

  <div class="video" role="img" aria-label="Video still of a team joining hands in a circle"></div>
  <div class="video-bar">0:00 / 0:47</div>

  <section class="news">
    <div class="news-date"><b>AUG</b>12</div>
    <p><strong>Duis aute irure dolor</strong> in reprehenderit in voluptate velit esse cillum dolore eu fugiat nulla pariatur. Excepteur sint occaecat cupidatat non proident, sunt in culpa qui officia deserunt mollit anim lorem ipsum lorem ispm.</p>
    <a>View All &gt;&gt;</a>
  </section>

  <footer class="footer">
    <h3 style="left:141px;top:18px">Quick Links</h3>
    <ul class="quick-links">
      <li>HOME</li><li>ARTICLES</li><li>ABOUT US</li><li>CLIENTS</li><li>WHAT WE DO</li><li>PARTNERS</li><li>NEWS BLOG</li><li>CONTACT US</li>
    </ul>
    <div class="divider" style="left:399px"></div>

    <h3 style="left:430px;top:18px">Quick Contact</h3>
    <div class="field" style="top:50px">Name</div>
    <div class="field" style="top:86px">Email</div>
    <div class="field" style="top:122px;height:48px">Message</div>
    <div class="btn" style="left:423px;top:180px;width:73px;height:25px">Submit</div>
    <div class="divider" style="left:703px"></div>

    <h3 style="left:730px;top:18px">Contact Info</h3>
    <div class="info" style="top:60px"><svg width="16" height="20" viewBox="0 0 16 20"><path d="M8 1a6 6 0 0 1 6 6c0 5-6 12-6 12S2 12 2 7a6 6 0 0 1 6-6z" fill="#d8ae00"/><circle cx="8" cy="7" r="2" fill="#93004c"/></svg><span>Lorem ipsum dolor sit<br>amet, consectetuer<br>adipiscing elit.</span></div>
    <div class="info" style="top:126px"><svg width="16" height="16" viewBox="0 0 16 16"><circle cx="8" cy="8" r="7" fill="none" stroke="#d8ae00" stroke-width="1.5"/><path d="M5 4l2 2-1 1 3 3 1-1 2 2-2 1c-3 0-6-3-6-6z" fill="#d8ae00"/></svg><span>020 4410 2291</span></div>
    <div class="info" style="top:160px"><svg width="16" height="12" viewBox="0 0 16 12"><rect width="16" height="12" fill="#d8ae00"/><path d="M0 0l8 6 8-6" fill="none" stroke="#93004c" stroke-width="1.5"/></svg><span>info@plumbwick.net</span></div>
    <div class="divider" style="left:957px"></div>
    <div class="footer-mark" role="img" aria-label="Faint company table logo"></div>

    <h3 style="left:143px;top:246px">News Letter</h3>
    <div class="newsletter">Enter e-mail</div>
    <div class="btn" style="left:461px;top:248px;width:74px;height:25px">Submit</div>
    <h3 style="left:597px;top:246px">Follow us</h3>
    <div class="social" style="left:699px"></div>
    <div class="social" style="left:744px"></div>
    <div class="social" style="left:783px"></div>
  </footer>

  <div class="copyright">© 2014 plumbwick. All Rights Reserved.</div>
</div>
</body>
</html>
```